Business card design for web travel company

Hi
we'd like to receive some proposal for a business card design.
Stayvora is a private travel club, dedicated to all travel lovers, with unique offers for exclusive destinations all around the world. At Stayvora you can find a wide range of offers for resorts, boutique hotels and travel packages at the best guaranteed price available on the market. The convenience of the offer is guaranteed by a private sales model: offers are available for a limited time only and they are personally chosen by Stayvora's qualified team of travel experts.
We offer only exclusive hotels with discounted prices but we are not an outlet or a discount supermarket: the design should reflect our connection with luxury, exclusivity using the same style of our website www.stayvora-example.com.
We want to make sure that when we'll present ourself to our business partner they will feel immediately which is our brand positioning giving them also a sense of an affordable and reliable partner.
In attachment you can also find our brand guidelines (please note that we are NOT USING ANY MORE THE TAG LINE "Five star outlet" mentioned in it).
The info to be inserted are:
Name Surname
Job Title
Tel
Mobile (when needed)
Email
Stayvora S.r.l.
Via Bruno Salvi 27
20139 Milano

```html
<!DOCTYPE html>
<html lang="en">
<head>
<meta charset="utf-8">
<title>Stayvora — Business Card</title>
<link rel="stylesheet" href="https://fonts.googleapis.com/css2?family=Archivo:wght@400;700&display=swap">
<style>
  :root {
    --page-bg: #e9e6e3;
    --card-black: #050505;
    --card-sheen: #151515;
    --band-dark: #3a3a3a;
    --band-mid: #9a9a9a;
    --band-light: #ffffff;
    --ink: #0a0a0a;
    --text-light: #ffffff;
    --text-soft: #d9d9d9;
    --url-grey: #e6e6e6;
    --accent-gold: #c9b07a;
  }
  * { margin: 0; padding: 0; box-sizing: border-box; }
  html, body {
    width: 1200px; height: 900px; overflow: hidden;
    background: var(--page-bg);
    font-family: "Archivo", Arial, sans-serif;
  }
  .canvas { position: relative; width: 1200px; height: 900px; }

  .card {
    position: absolute; top: 307px;
    width: 501px; height: 286px;
    border-radius: 14px; overflow: hidden;
    background: var(--card-black);
  }
  .card--front { left: 77px; }
  .card--back { left: 627px; }

  .card__texture {
    position: absolute; inset: 0;
    background: linear-gradient(135deg, var(--card-black) 0%, var(--card-sheen) 50%, var(--card-black) 100%);
  }

  .brand-band {
    position: absolute; left: 0; right: 0; top: 112px; height: 65px;
    display: flex; align-items: center;
  }
  .card--front .brand-band {
    justify-content: flex-end; padding-right: 18px;
    background: linear-gradient(90deg, var(--band-dark) 0%, var(--band-mid) 25%, var(--band-light) 58%, var(--band-light) 100%);
  }
  .card--back .brand-band {
    justify-content: space-between; padding: 0 18px 0 33px;
    background: linear-gradient(90deg, var(--band-light) 0%, var(--band-light) 50%, var(--band-mid) 75%, var(--band-dark) 100%);
  }
  .brand-name {
    font-weight: 400; font-size: 44px; line-height: 1;
    color: var(--ink); letter-spacing: 0.5px;
  }
  .brand-url {
    font-size: 14px; letter-spacing: 2px;
    color: var(--url-grey); font-weight: 400;
  }

  .holder {
    position: absolute; left: 31px; top: 193px;
    color: var(--text-light);
  }
  .holder__name { font-weight: 700; font-size: 21px; letter-spacing: 0.3px; }
  .holder__contacts { list-style: none; margin-top: 13px; }
  .holder__contacts li {
    display: flex; align-items: center; gap: 4px;
    font-size: 12.5px; color: var(--text-soft); line-height: 18px;
  }
  .contact-icon { width: 14px; height: 11px; flex: none; }
</style>
</head>
<body>
<main class="canvas">
  <section class="card card--front" aria-label="Card front">
    <div class="card__texture" role="img" aria-label="Black card background with fine diagonal pinstripe texture"></div>
    <div class="brand-band">
      <span class="brand-name">Stayvora</span>
    </div>
    <div class="holder">
      <p class="holder__name">Marco Dellavalle</p>
      <ul class="holder__contacts">
        <li>
          <svg class="contact-icon" viewBox="0 0 14 11" aria-hidden="true">
            <path d="M1 4 Q7 0 13 4 L11 5 L9.5 3.6 L4.5 3.6 L3 5 Z" fill="var(--accent-gold)"/>
            <rect x="3.5" y="5.5" width="7" height="4.5" rx="1" fill="var(--accent-gold)"/>
          </svg>
          <span>: +23 4560 7890</span>
        </li>
        <li>
          <svg class="contact-icon" viewBox="0 0 14 11" aria-hidden="true">
            <rect x="1.5" y="1.5" width="11" height="8" fill="none" stroke="var(--accent-gold)" stroke-width="1"/>
            <path d="M1.5 1.5 L7 6 L12.5 1.5 M1.5 9.5 L5.5 5 M12.5 9.5 L8.5 5" fill="none" stroke="var(--accent-gold)" stroke-width="1"/>
          </svg>
          <span>: marco@stayvora-example.com</span>
        </li>
      </ul>
    </div>
  </section>

  <section class="card card--back" aria-label="Card back">
    <div class="card__texture" role="img" aria-label="Black card background with fine diagonal pinstripe texture"></div>
    <div class="brand-band">
      <span class="brand-name">Stayvora</span>
      <span class="brand-url">www.stayvora-example.com</span>
    </div>
  </section>
</main>
</body>
</html>
```